Playful Website Design Needed Pet Sitting and Dog Walking Business

Need a simple one page Web Design Built on WordPress.
Sections:

About Us
Services Provided
Costs
Contact Us
Intake Form (Questionnaire that goes to email)
See us in Action

Industry/Entity Type

Pet Sitting and Dog Walking

Number of Pages Required

1 page

Font styles to use
Other font styles liked:
• See the Business Card Font and use that.

Colors
EE7325
F08F49
F5BC92
FAE3D3
FDF4ED

Requirements
Must have
• See attached Logo Design, with Font's and Colors Use these as theme guide

```html
<!DOCTYPE html>
<html lang="en">
<head>
<meta charset="utf-8">
<title>Paw Pals Care – Pet Sitting</title>
<link href="https://fonts.googleapis.com/css2?family=Mali:wght@400;600;700&display=swap" rel="stylesheet">
<style>
:root{
  --orange:#EE7325;
  --orange-mid:#F08F49;
  --peach:#F5BC92;
  --blush:#FAE3D3;
  --cream:#FDF4ED;
  --green:#6BAE3A;
  --ink:#2b2b2b;
  --muted:#555;
  --dark:#1c1c1c;
  --white:#fff;
}
*{box-sizing:border-box;margin:0;padding:0}
html,body{width:1200px;height:3352px;overflow:hidden}
body{font-family:"Mali",cursive;color:var(--ink);background:var(--white);position:relative}
.abs{position:absolute}
/* hero */
.hero{position:absolute;left:0;top:0;width:1200px;height:668px;background:linear-gradient(180deg,#6d6a66 0%,#8a7a63 45%,#5b4b3a 100%)}
.hero-art{position:absolute;inset:0}
.hero-shade{position:absolute;inset:0;background:rgba(0,0,0,.35)}
.brand{position:absolute;left:34px;top:26px;display:flex;align-items:center;gap:8px;font-weight:700;font-size:22px;color:var(--orange)}
.brand .dot{width:30px;height:30px;border-radius:50%;background:var(--green)}
.nav{position:absolute;right:60px;top:0;display:flex;background:var(--orange);height:44px}
.nav a{color:var(--white);text-decoration:none;font-size:16px;padding:12px 16px}
.nav a.active{background:var(--white);color:var(--orange);border-radius:0 0 4px 4px}
.hero-text{position:absolute;left:0;right:0;top:100px;text-align:center;color:var(--white)}
.hero-text h1{font-size:50px;font-weight:700}
.hero-text p{font-size:19px;width:460px;margin:18px auto 0;line-height:1.45;font-weight:600}
.btn{display:inline-block;background:var(--orange);color:var(--white);border-radius:20px;padding:8px 22px;font-size:15px;font-weight:600}
.hero-text .btn{margin-top:30px}
.dots{position:absolute;left:0;right:0;top:622px;display:flex;justify-content:center;gap:8px}
.dots i{width:9px;height:9px;border-radius:50%;background:rgba(255,255,255,.6)}
.dots i:first-child{background:var(--white)}
/* about */
.about-text{left:128px;top:726px;width:340px;display:flex;flex-direction:column;align-items:flex-start}
.about-eyebrow{font-size:24px;font-weight:700;line-height:1.3}
.about-title{font-size:38px;font-weight:700;color:var(--orange);line-height:1.2;margin-top:2px}
.about-title span{color:var(--green)}
.about-copy{margin-top:40px;font-size:13.5px;line-height:1.5;color:var(--muted)}
.about-btn{margin-top:22px}
.circle-photo{border-radius:50%}
.flower{left:760px;top:720px;width:240px;height:410px;border-radius:120px 120px 20px 20px;background:linear-gradient(180deg,var(--orange-mid),#f5c84a 55%,#7cbf4a)}
/* features */
.features{left:128px;top:1196px;width:946px;display:flex;gap:12px}
.pill{flex:1;background:var(--orange-mid);color:var(--white);border-radius:8px;height:40px;display:flex;align-items:center;justify-content:center;gap:6px;font-size:13px;font-weight:600}
.pill i{width:14px;height:14px;border-radius:50%;background:var(--white)}
/* services */
.services{left:0;top:1252px;width:1200px;height:560px;background:var(--cream)}
.section-title{position:absolute;left:0;right:0;text-align:center;font-size:28px;font-weight:700}
.services .section-title{top:28px}
.services-photo{left:128px;top:118px;width:482px;height:406px;border-radius:4px;background:linear-gradient(135deg,#7a9a5c,#a4b07a 50%,#5f4a33)}
.service-list{left:650px;top:90px;width:425px}
.service{display:flex;gap:22px;padding:14px 0;border-bottom:1px solid var(--peach);height:112px}
.service:last-child{border-bottom:none}
.service-icon{width:56px;height:50px;flex:none;border-radius:10px;background:var(--orange)}
.service h3{font-size:17px;font-weight:700;margin-bottom:6px}
.service p{font-size:13px;line-height:1.45;color:var(--muted)}
/* cost band */
.cost{left:0;top:1820px;width:1200px;height:120px;background:var(--orange);color:var(--white);font-size:34px;font-weight:700;display:flex;align-items:center;justify-content:center}
/* contact */
.contact{left:0;top:1940px;width:1200px;height:580px;background:linear-gradient(180deg,#5d7fa8 0%,#9ca4a6 35%,#c7b28d 70%,#b39a74 100%)}
.contact-card{left:130px;top:80px;width:280px;height:420px;background:var(--white);border-radius:6px;padding:30px 30px}
.contact-card h2{font-size:27px;font-weight:700;border-left:3px solid var(--green);padding-left:12px;margin-bottom:34px}
.info{display:flex;gap:14px;margin-bottom:32px;font-size:15px;line-height:1.5}
.info .ico{width:28px;height:28px;flex:none;border-radius:50%;background:var(--green);display:flex;align-items:center;justify-content:center}
.info b{font-weight:700;display:block}
/* booking */
.booking{left:0;top:2520px;width:1200px;height:592px;background:linear-gradient(180deg,#3a3836,#2b2a28)}
.booking .section-title{top:34px;color:var(--white)}
.form{left:330px;top:120px;width:540px;height:420px;background:#e9e9e9;border-radius:6px;padding:24px 40px}
.grid{display:grid;grid-template-columns:1fr 1fr;column-gap:36px;row-gap:14px}
.field label{display:block;font-size:12px;margin-bottom:5px}
.field .input{height:32px;background:var(--white);border:1px solid #ccc;border-radius:4px;font-size:12px;color:#999;padding:8px 10px;display:flex;justify-content:space-between}
.submit{display:block;width:90px;margin:26px auto 0;text-align:center;padding:7px 0}
/* footer */
.footer{left:0;top:3112px;width:1200px;height:240px;background:#050505;color:var(--white)}
.footer .brand{left:130px;top:78px;font-size:30px}
.footer .brand .dot{width:40px;height:40px}
.follow{right:130px;top:54px;display:flex;align-items:center;gap:8px;font-size:14px}
.follow i{width:22px;height:22px;border-radius:3px;display:block}
.foot-nav{right:130px;top:110px;display:flex;gap:32px;font-size:16px;border-bottom:1px solid #555;padding-bottom:14px}
.copy{right:130px;top:184px;font-size:13px}
</style>
</head>
<body>

<header class="hero">
  <div class="hero-art" role="img" aria-label="Dog walker holding leashes of many dogs on a path"></div>
  <div class="hero-shade"></div>
  <div class="brand"><span class="dot"></span>Paw Pals Care</div>
  <nav class="nav">
    <a class="active">Home</a><a>About Us</a><a>Services</a><a>Costs</a><a>Contact Us</a>
  </nav>
  <div class="hero-text">
    <h1>Pet Sitting</h1>
    <p>Lorem Ipsum is simply dummy text of the printing and typesetting industry</p>
    <span class="btn">Read More</span>
  </div>
  <div class="dots"><i></i><i></i><i></i><i></i><i></i></div>
</header>

<section>
  <div class="abs about-text">
    <div class="about-eyebrow">About</div>
    <h2 class="about-title">Paw <span>Pals</span> Care</h2>
    <p class="about-copy">There are many variations of passages of Lorem Ipsum available, but the majority have suffered alteration in some form, by injected humour, or randomised words which don't look even slightly believable. If you are going to use a passage of Lorem Ipsum, you need to be sure there isn't anything embarrassing hidden in the middle of text. All the Lorem Ipsum generators on the Internet tend to repeat predefined chunks as necessary, making this the first true generator on the Internet.</p>
    <span class="btn about-btn">Read More</span>
  </div>
  <div class="abs circle-photo" style="left:586px;top:720px;width:124px;height:124px;background:linear-gradient(135deg,#8aa06a,#c9b28a)" role="img" aria-label="Person hugging a dog"></div>
  <div class="abs circle-photo" style="left:545px;top:868px;width:124px;height:124px;background:linear-gradient(135deg,#6e9a4a,#b9c58c)" role="img" aria-label="Woman walking a dog on grass"></div>
  <div class="abs circle-photo" style="left:672px;top:1004px;width:124px;height:124px;background:linear-gradient(135deg,#b08a66,#e0c9a8)" role="img" aria-label="Sitter with a small dog indoors"></div>
  <div class="abs flower" role="img" aria-label="Playful cartoon flower with a cat character"></div>
  <div class="abs features">
    <div class="pill"><i></i>Exceptional Staff</div>
    <div class="pill"><i></i>Fully insured team</div>
    <div class="pill"><i></i>Meet your pet sitter</div>
    <div class="pill"><i></i>Customized Services</div>
    <div class="pill"><i></i>Reasonable Rates</div>
  </div>
</section>

<section class="abs services">
  <h2 class="section-title">Our Services</h2>
  <div class="abs services-photo" role="img" aria-label="Woman sitting on a path with two dogs"></div>
  <div class="abs service-list">
    <div class="service"><div class="service-icon" role="img" aria-label="Puppy icon"></div><div><h3>Puppy Sitting</h3><p>There are many variations of passages of Lorem Ipsum available, but the majority have suffered alteration in some form, by injected humour.</p></div></div>
    <div class="service"><div class="service-icon" role="img" aria-label="Dog walking icon"></div><div><h3>Dog Walking</h3><p>There are many variations of passages of Lorem Ipsum available, but the majority have suffered alteration in some form, by injected humour.</p></div></div>
    <div class="service"><div class="service-icon" role="img" aria-label="Special care icon"></div><div><h3>Specialty Care</h3><p>There are many variations of passages of Lorem Ipsum available, but the majority have suffered alteration in some form, by injected humour.</p></div></div>
    <div class="service"><div class="service-icon" role="img" aria-label="Pet bowl icon"></div><div><h3>Drop-in Visits</h3><p>There are many variations of passages of Lorem Ipsum available, but the majority have suffered alteration in some form, by injected humour.</p></div></div>
  </div>
</section>

<div class="abs cost">$8 per Visit | 2 Visits a day</div>

<section class="abs contact" role="img" aria-label="Walker with two spaniels on red leashes on a sandy path">
  <div class="abs contact-card">
    <h2>Contact Us</h2>
    <div class="info"><span class="ico"><svg width="14" height="14" viewBox="0 0 24 24"><path fill="#fff" d="M12 2a7 7 0 0 0-7 7c0 5 7 13 7 13s7-8 7-13a7 7 0 0 0-7-7zm0 9.5A2.5 2.5 0 1 1 12 6.5a2.5 2.5 0 0 1 0 5z"/></svg></span><div><b>Location</b>214 Maple Lane<br>Riverton, CT 06065</div></div>
    <div class="info"><span class="ico"><svg width="14" height="14" viewBox="0 0 24 24"><path fill="#fff" d="M6.6 10.8a15 15 0 0 0 6.6 6.6l2.2-2.2a1 1 0 0 1 1-.25 11.4 11.4 0 0 0 3.6.6 1 1 0 0 1 1 1V20a1 1 0 0 1-1 1A17 17 0 0 1 3 4a1 1 0 0 1 1-1h3.5a1 1 0 0 1 1 1c0 1.25.2 2.45.6 3.6a1 1 0 0 1-.25 1z"/></svg></span><div><b>Call Us</b>+1 555 014 2230</div></div>
    <div class="info"><span class="ico"><svg width="14" height="14" viewBox="0 0 24 24"><path fill="#fff" d="M3 5h18v14H3zm2 2v.5l7 4.5 7-4.5V7l-7 4.5z"/></svg></span><div><b>Email Us</b>hello@pawpalscare.com</div></div>
  </div>
</section>

<section class="abs booking">
  <h2 class="section-title">Book trusted sitters and dog walkers.</h2>
  <form class="abs form">
    <div class="grid">
      <div class="field"><label>Name</label><div class="input">Type Full Name</div></div>
      <div class="field"><label>Phone Number</label><div class="input">+1 555 014 2230</div></div>
      <div class="field"><label>Boarding start</label><div class="input">Enter start date</div></div>
      <div class="field"><label>Select Service</label><div class="input">Dog Sitting<span>▾</span></div></div>
      <div class="field"><label>Per Home Stays</label><div class="input">Drop off</div></div>
      <div class="field"><label>Select Service</label><div class="input">Pick up<span>▾</span></div></div>
      <div class="field"><label>Dog Size</label><div class="input">Drop off</div></div>
      <div class="field"><label>Subject</label><div class="input">Select<span>▾</span></div></div>
    </div>
    <span class="btn submit">Submit</span>
  </form>
</section>

<footer class="abs footer">
  <div class="brand"><span class="dot"></span>Paw Pals Care</div>
  <div class="abs follow">Follow us <i style="background:#3b5bb5"></i><i style="background:#2aa3e0"></i><i style="background:#c9357a"></i><i style="background:#d9302b"></i></div>
  <nav class="abs foot-nav"><span>Home</span><span>About Us</span><span>Services</span><span>Costs</span><span>Contact Us</span></nav>
  <div class="abs copy">Copyright © 2022 All Rights Reserved</div>
</footer>

</body>
</html>
```